Film Company needs Poster Design Project for upcoming film "MARSH"

At Larkhollow Films, we need a poster design for our upcoming feature film project "MARSH," America first 'rock and roll' star. Our film will cover Silas Wendell Marsh's life his drinking, passion and writing. It will not be a horror film, but rather a biopic on his life.
Larkhollow Films is a full service film and television production company, founded by Dennis Whitby and Ventroma, LLC in 2006. Larkhollow Films’ mission is to blend artistic talent with engaging stories to create feature films and television that delight audiences of all ages.
We would like to see designs that embody Silas Wendell Marsh as a person. The film will cover most of his famous poems/novels/short stories so any reference to "Hollow lantern" or "The Marten," etc...would work.
Thank you ALL for the amazing work you have submitted, you made it really hard for me to come up with one choice. I will make my decision by Wednesday.
Target audience 18 - 35
It Company

```html
<!DOCTYPE html>
<html lang="en">
<head>
<meta charset="utf-8">
<title>MARSH — Larkhollow Films</title>
<link rel="stylesheet" href="https://fonts.googleapis.com/css2?family=Archivo+Black&family=Oswald:wght@500;600&family=Montserrat:wght@600;700&display=swap">
<style>
  :root {
    --bg: #2e2318;
    --olive: #4a4919;
    --olive-edge: #5e5d24;
    --veil: rgba(190, 190, 180, 0.55);
    --frame: #9c9c94;
    --rust: #6e3414;
    --rust-deep: #5a2a10;
    --title: #6b3612;
    --ink: #0d0b08;
    --sepia-light: #a9a06a;
    --sepia-dark: #2b2a14;
    --amber-light: #d99a5c;
    --amber-dark: #4a1e0c;
    --logo-box: #a8a8a3;
    --logo-text: #c98a1c;
  }
  html, body {
    margin: 0;
    padding: 0;
    overflow: hidden;
    background: var(--bg);
  }
  .poster {
    position: relative;
    width: 800px;
    height: 1200px;
    background: var(--bg);
    overflow: hidden;
  }
  .poster svg { display: block; }
  .presents { font-family: "Oswald", sans-serif; font-weight: 500; fill: var(--rust); }
  .title { font-family: "Archivo Black", sans-serif; fill: var(--title); }
  .tagline { font-family: "Montserrat", sans-serif; font-weight: 700; fill: var(--ink); }
  .tagline-warp { font-family: "Oswald", sans-serif; font-weight: 600; fill: var(--ink); }
  .biopic { font-family: "Oswald", sans-serif; font-weight: 500; fill: var(--rust-deep); }
  .themes { font-family: "Montserrat", sans-serif; font-weight: 600; fill: var(--ink); }
  .studio-name { font-family: "Oswald", sans-serif; font-weight: 600; fill: var(--logo-text); }
</style>
</head>
<body>
<div class="poster">
  <svg width="800" height="1200" viewBox="0 0 800 1200" xmlns="http://www.w3.org/2000/svg">
    <defs>
      <linearGradient id="sepiaPortrait" x1="0" y1="0" x2="0" y2="1">
        <stop offset="0" stop-color="var(--sepia-dark)"/>
        <stop offset="0.45" stop-color="var(--sepia-light)"/>
        <stop offset="1" stop-color="var(--sepia-dark)"/>
      </linearGradient>
      <radialGradient id="amberPortrait" cx="0.5" cy="0.6" r="0.6">
        <stop offset="0" stop-color="var(--amber-light)"/>
        <stop offset="1" stop-color="var(--amber-dark)"/>
      </radialGradient>
      <filter id="panelShadow" x="-5%" y="-5%" width="110%" height="110%">
        <feDropShadow dx="3" dy="4" stdDeviation="4" flood-color="#000" flood-opacity="0.6"/>
      </filter>
      <filter id="titleBevel" x="-5%" y="-5%" width="110%" height="115%">
        <feDropShadow dx="2" dy="3" stdDeviation="2" flood-color="#000" flood-opacity="0.55"/>
      </filter>
      <path id="warpArc" d="M195 800 Q 470 870 755 790"/>
    </defs>

    <!-- bird silhouette on the top edge -->
    <rect class="bird" x="45" y="18" width="235" height="85" fill="#0b0907" opacity="0.9" rx="30"
          role="img" aria-label="Silhouette of a black bird perched above the portrait"/>

    <!-- main olive panel -->
    <rect class="panel" x="32" y="125" width="748" height="772" fill="var(--olive)" stroke="var(--olive-edge)" stroke-width="4" filter="url(#panelShadow)"/>

    <!-- left portrait with translucent veil -->
    <rect class="veil" x="38" y="108" width="315" height="302" fill="var(--veil)"/>
    <g transform="rotate(-1.5 194 258)">
      <rect class="portrait portrait--sepia" x="60" y="117" width="270" height="285" fill="url(#sepiaPortrait)"
            role="img" aria-label="Sepia portrait of Silas Wendell Marsh"/>
    </g>

    <!-- right portrait, inverted, in grey frame -->
    <rect class="frame" x="455" y="158" width="310" height="302" fill="var(--frame)"/>
    <g transform="rotate(2 612 308)">
      <rect class="portrait portrait--amber" x="477" y="166" width="272" height="286" fill="url(#amberPortrait)"
            role="img" aria-label="Upside-down amber-toned portrait of Silas Wendell Marsh"/>
    </g>

    <!-- presenter -->
    <text class="presents" x="318" y="468" font-size="42" text-anchor="middle" textLength="182" lengthAdjust="spacingAndGlyphs">LARKHOLLOW</text>
    <text class="presents" x="365" y="522" font-size="42" text-anchor="middle" textLength="170" lengthAdjust="spacingAndGlyphs">PRESENTS</text>

    <!-- title -->
    <text class="title" x="392" y="688" font-size="158" text-anchor="middle" textLength="500" lengthAdjust="spacingAndGlyphs" filter="url(#titleBevel)">MARSH</text>

    <!-- tagline -->
    <text class="tagline" x="453" y="752" font-size="52" text-anchor="middle" textLength="536" lengthAdjust="spacingAndGlyphs" transform="rotate(2 453 740)">AMERICA’S FIRST</text>
    <text class="tagline-warp" font-size="62">
      <textPath href="#warpArc" textLength="555" lengthAdjust="spacingAndGlyphs">ROCK AND ROLL STAR</textPath>
    </text>

    <!-- biopic line -->
    <text class="biopic" x="400" y="988" font-size="56" text-anchor="middle" textLength="738" lengthAdjust="spacingAndGlyphs">A BIOPIC ON THE LIFE OF SILAS WENDELL MARSH</text>
    <text class="themes" x="400" y="1021" font-size="25" text-anchor="middle" textLength="590" lengthAdjust="spacingAndGlyphs">HIS DRINKING, PASSION AND WRITING</text>

    <!-- studio mark -->
    <rect class="studio-box" x="627" y="1035" width="152" height="152" fill="var(--logo-box)"/>
    <text class="studio-name" x="703" y="1108" font-size="22" text-anchor="middle">LARKHOLLOW</text>
    <text class="studio-name" x="703" y="1134" font-size="22" text-anchor="middle">FILMS</text>
  </svg>
</div>
</body>
</html>
```